Looking for a dynamic business card for a pizzeria.

A business card with our food, logo, and space for name, title, email, website, phone. The card should convey quality, unique, amazing. On the front, I envision food photo or photos with the owners names and contact information. On the back, more food with locations, website, facebook, twitter, instagram icons. It should look polished, not cartoonish, or plain.
Target Market(s)
upscale, local food buyers, 30-50 years in age.
Industry/Entity Type
Restaurant
Contact Information for Business Card
Business Name: Bru'nettix, LLC
Website: www.brunettix.com
Back:
2 locations: (can list on the back of card)
1. Harborside
4087 Corlan Avenue
Lindmoor, OR 97412
360-481-5067
2. Crestview Hill
7315 Wendmere Road
Lindmoor, OR 97418
360-293-8840
front:
EDITABLE space for
Business name
Person's Name
title
2nd title
Email address
cell-phone number
Requirements
Must have
- logo
- my food photo or photos (no watermarks showing)
- locations on back
- Person contact information on front
- full bleed

```html
<!DOCTYPE html>
<html lang="en">
<head>
<meta charset="utf-8">
<title>Bru'nettix, LLC — Business Card</title>
<link rel="stylesheet" href="https://fonts.googleapis.com/css2?family=Open+Sans:wght@400;600;700&display=swap">
<style>
  :root {
    --bg: #e9e6e1;
    --green-light: #2f7a45;
    --green-dark: #103a1f;
    --white: #ffffff;
    --white-soft: rgba(255,255,255,0.85);
    --photo-cream: #e8ddd0;
    --photo-pepperoni: #b5533e;
    --photo-deep: #7d2c20;
    --shadow: rgba(0,0,0,0.25);
  }
  * { box-sizing: border-box; margin: 0; padding: 0; }
  html, body {
    width: 1200px; height: 913px; overflow: hidden;
    background: var(--bg);
    font-family: "Open Sans", Arial, sans-serif;
  }
  .canvas {
    position: relative; width: 1200px; height: 913px;
    display: flex; align-items: center; justify-content: center; gap: 50px;
  }
  .card {
    position: relative; width: 525px; height: 300px;
    border-radius: 18px; overflow: hidden;
    box-shadow: 0 10px 28px var(--shadow);
    color: var(--white);
  }

  /* Front: contact card */
  .card--front {
    background: linear-gradient(135deg, var(--green-light) 0%, var(--green-dark) 100%);
  }
  .brand {
    position: absolute; left: 34px; top: 92px; width: 230px;
    display: flex; flex-direction: column; align-items: flex-start;
  }
  .brand__mark { display: flex; align-items: center; gap: 12px; }
  .brand__dot {
    width: 46px; height: 46px; border-radius: 50%;
    border: 3px solid var(--white); flex: none;
  }
  .brand__name { font-size: 34px; font-weight: 600; letter-spacing: 1px; line-height: 1; }
  .brand__legal { margin-top: 14px; font-size: 25px; font-weight: 700; letter-spacing: 1px; }
  .divider {
    position: absolute; left: 282px; top: 48px;
    width: 1px; height: 204px; background: var(--white-soft);
  }
  .contact { position: absolute; left: 302px; top: 78px; width: 210px; }
  .contact__name { font-size: 21px; font-weight: 700; letter-spacing: 0.5px; line-height: 1.1; }
  .contact__title { font-size: 12px; margin-bottom: 12px; color: var(--white-soft); }
  .contact__row { display: flex; align-items: center; gap: 7px; font-size: 12.5px; line-height: 1.75; }
  .contact__row svg { width: 11px; height: 11px; flex: none; }

  /* Back: locations card */
  .card--back { background: var(--photo-deep); }
  .photo {
    position: absolute; inset: 0;
    background:
      radial-gradient(ellipse at 80% 12%, var(--photo-cream) 0%, transparent 45%),
      radial-gradient(ellipse at 30% 75%, var(--photo-pepperoni) 0%, transparent 60%),
      linear-gradient(160deg, var(--photo-cream) 0%, var(--photo-pepperoni) 45%, var(--photo-deep) 100%);
  }
  .photo::after { content: ""; position: absolute; inset: 0; background: rgba(0,0,0,0.22); }
  .locations {
    position: absolute; left: 140px; top: 40px; width: 360px;
    display: flex; flex-direction: column; align-items: flex-start;
  }
  .locations .brand__legal { margin-top: 10px; margin-bottom: 10px; }
  .location { font-size: 13.5px; line-height: 1.4; padding-left: 70px; }
  .location + .location { margin-top: 4px; }
</style>
</head>
<body>
<main class="canvas">

  <section class="card card--front" aria-label="Business card front">
    <div class="brand">
      <div class="brand__mark">
        <span class="brand__dot"></span>
        <span class="brand__name">Bru'nettix</span>
      </div>
      <div class="brand__legal">BRU'NETTIX, LLC</div>
    </div>
    <div class="divider"></div>
    <div class="contact">
      <p class="contact__name">MARCO DELLING</p>
      <p class="contact__title">Director, President</p>
      <p class="contact__row">
        <svg viewBox="0 0 24 24" fill="none" stroke="currentColor" stroke-width="2.4"><path d="M5 3h4l2 5-3 2a12 12 0 0 0 6 6l2-3 5 2v4a2 2 0 0 1-2 2A18 18 0 0 1 3 5a2 2 0 0 1 2-2z"/></svg>
        360-512-7764
      </p>
      <p class="contact__row">
        <svg viewBox="0 0 24 24" fill="none" stroke="currentColor" stroke-width="2.4"><rect x="3" y="5" width="18" height="14" rx="1"/><path d="M3 6l9 7 9-7"/></svg>
        info@marcodelling.com
      </p>
      <p class="contact__row">
        <svg viewBox="0 0 24 24" fill="none" stroke="currentColor" stroke-width="2.4"><circle cx="12" cy="12" r="9"/><path d="M3 12h18M12 3c3 3 3 15 0 18M12 3c-3 3-3 15 0 18"/></svg>
        www.brunettix.com
      </p>
    </div>
  </section>

  <section class="card card--back" aria-label="Business card back">
    <div class="photo" role="img" aria-label="Close-up photo of a pepperoni pizza with melted cheese"></div>
    <div class="locations">
      <div class="brand__mark">
        <span class="brand__dot"></span>
        <span class="brand__name">Bru'nettix</span>
      </div>
      <div class="brand__legal">BRU'NETTIX, LLC</div>
      <p class="location">360-481-5067<br>Harborside 4087 Corlan Avenue<br>Lindmoor, OR 97412</p>
      <p class="location">360-293-8840<br>Crestview Hill 7315 Wendmere Road<br>Lindmoor, OR 97418</p>
    </div>
  </section>

</main>
</body>
</html>
```